Packing for Razor Blade VELUMOR

Dears: We need a packing design. The product is an Disposable Razor Blade. We are a company in Brazil.

The packing consists in a bag package which the Disposables Razos are placed. 5 units into each bag.

The bag is not 100% printed and should let a space to the customer see the razors inside. Some competitors uses oval circle. I attached competitor package (Dax Marino)

The background color should be blue, this color tonality should vary its magnitude from dark blue to soft blue. Blue is a good color for personal care products because customer can take the impression of cleanness, especially for razor blade which has the fuction to shave.

You can feel free to add other colors however it can not be much colorfull because it may get trouble to printer company print it. Silver is good.

You can feel free to do details. You can feel free also to place the logo above the package or at bottom of it.

Dimmensions:
Heigh 24cm
Width 10cm

Featuring
- Featuring: Handle with Grip. In Portuguese - (Cabo Aderente)
- Featuring: 2 Razors. In portuguese - (Duas Lâminas)

Reason: I stayed many days with out providing feedbacks. I want to give more time for you .

Target Market(s)

Mans ( for woman we will design other package )

Requirements
Nice to have
• maybe some tears as a wet surface...
pls can feel free

```html
<!DOCTYPE html>
<html lang="pt-BR">
<head>
<meta charset="UTF-8">
<title>VELUMOR Trix 5 – Embalagem</title>
<link rel="stylesheet" href="https://fonts.googleapis.com/css2?family=Exo+2:ital,wght@0,800;1,800;1,900&display=swap">
<style>
  :root {
    --blue-sky: #3d93f5;
    --blue-mid: #1446e6;
    --blue-deep: #0a1fb0;
    --navy: #020c52;
    --navy-dark: #010838;
    --white: #ffffff;
    --silver-light: #f4f6fa;
    --silver-mid: #b9c0cc;
    --silver-dark: #7d8694;
  }
  html, body {
    margin: 0;
    padding: 0;
    width: 1200px;
    height: 2862px;
    overflow: hidden;
    background: var(--white);
  }
  .package {
    position: relative;
    width: 1200px;
    height: 2862px;
    overflow: hidden;
    background: linear-gradient(180deg,
      var(--blue-sky) 0%,
      var(--blue-mid) 40%,
      var(--blue-deep) 62%,
      var(--navy) 82%,
      var(--navy-dark) 100%);
    font-family: "Exo 2", "Arial Black", sans-serif;
  }
  .brand {
    position: absolute;
    top: 200px;
    left: 0;
    width: 100%;
    text-align: center;
    font-weight: 800;
    font-style: normal;
    font-size: 150px;
    letter-spacing: 8px;
    color: var(--silver-light);
    line-height: 1;
  }
  .product-name {
    position: absolute;
    top: 640px;
    left: 0;
    width: 100%;
    text-align: center;
    font-weight: 900;
    font-style: italic;
    font-size: 165px;
    letter-spacing: 14px;
    line-height: 1;
    background: linear-gradient(180deg, var(--silver-light) 0%, var(--silver-mid) 55%, var(--silver-dark) 100%);
    -webkit-background-clip: text;
    background-clip: text;
    color: transparent;
  }
  .window {
    position: absolute;
    left: 0;
    top: 0;
    width: 1200px;
    height: 2862px;
  }
  .window-area { fill: var(--white); }
  .tag-corner { fill: var(--navy); }
  .tag-text {
    fill: var(--white);
    font-family: "Exo 2", sans-serif;
    font-weight: 900;
    font-style: italic;
    font-size: 74px;
  }
  .badge-circle { fill: url(#badgeFill); stroke: var(--white); stroke-width: 5; }
  .badge-number {
    fill: var(--white);
    font-family: "Exo 2", sans-serif;
    font-weight: 900;
    font-style: italic;
    font-size: 190px;
  }
  .badge-label {
    fill: var(--white);
    font-family: "Exo 2", sans-serif;
    font-weight: 800;
    font-style: italic;
    font-size: 46px;
  }
  .features {
    position: absolute;
    top: 2410px;
    left: 200px;
    margin: 0;
    padding: 0;
    list-style: none;
    color: var(--white);
    font-weight: 900;
    font-style: italic;
    font-size: 92px;
    line-height: 88px;
  }
  .features li {
    position: relative;
    padding-left: 80px;
    margin-bottom: 22px;
  }
  .features li::before {
    content: "★";
    position: absolute;
    left: 0;
    top: 6px;
    font-size: 46px;
    font-style: normal;
  }
</style>
</head>
<body>
<main class="package">
  <div class="brand">VELUMOR</div>
  <div class="product-name">TRIX 5</div>

  <svg class="window" viewBox="0 0 1200 2862" xmlns="http://www.w3.org/2000/svg" aria-hidden="true">
    <defs>
      <radialGradient id="badgeFill" cx="45%" cy="35%" r="70%">
        <stop offset="0%" stop-color="#1a3fc8"/>
        <stop offset="100%" stop-color="#020c52"/>
      </radialGradient>
    </defs>
    <path class="window-area"
      d="M138 890 L1113 890
         C1030 1100 1025 1400 1085 1650
         C1135 1860 1110 2100 1105 2300
         L138 2300
         C128 2100 230 1850 195 1600
         C160 1350 140 1100 138 890 Z"/>
    <path class="tag-corner" d="M138 890 L405 890 L138 1115 Z"/>
    <text class="tag-text" x="172" y="1060" transform="rotate(-38 172 1060)">man</text>

    <circle class="badge-circle" cx="927" cy="2140" r="165"/>
    <text class="badge-number" x="927" y="2165" text-anchor="middle">5</text>
    <text class="badge-label" x="927" y="2232" text-anchor="middle">Aparelhos</text>
  </svg>

  <ul class="features">
    <li>Duas Lâminas<br>Paralelas</li>
    <li>Cabo Aderente</li>
  </ul>
</main>
</body>
</html>
```